Greeting Card Design - Bright Hearts Open Pages

Hi there

Thank you for taking the time to read about this project.

The project is for a range of greeting cards for the gay and lesbian community. The brand is called "Bright Hearts Open Pages".

In this project I require four designs in total (designs for homosexual couples, two for men and two for women). The designs need to reflect the general concept of being in love.

I am looking for variety (fun and funky, as well as modern and classy - please design to your tastes and I will give feedback).

I will work with each designer closely and provide the words for the cards as the designs are developed.

Thank you for considering this project.
Updates

I'm currently having issues with the craft huddle website and it won't let me upload files to show the logo. I will do so as soon as the website allows me. Thanks

Target Market(s)

Gay and lesbian community.

Industry/Entity Type

Community

Requirements
Must have
• I am looking for variety in the range. I would like designs that are modern and classy range; and also designs that are fun and funky.
Nice to have
• Hand drawings are good for the fun range, so is colour.
The classy range can be symbolic (e.g. holding hands) or black and whites.
Should not have
• Please do not use rainbows or rainbow coloured font.

```html
<!DOCTYPE html>
<html lang="en">
<head>
<meta charset="utf-8">
<title>Bright Hearts Open Pages – With your hand in mine</title>
<link href="https://fonts.googleapis.com/css2?family=Caveat:wght@400;600&display=swap" rel="stylesheet">
<style>
  :root {
    --card-red: #be1e2d;
    --paper: #ffffff;
    --ink: #333333;
    --rule: #555555;
    --photo-dark: #2a2a2a;
    --photo-mid: #6d6d6d;
    --photo-light: #bdbdbd;
  }
  html, body {
    margin: 0;
    padding: 0;
    width: 1200px;
    height: 794px;
    overflow: hidden;
    background: var(--paper);
  }
  .sheet {
    position: relative;
    width: 1200px;
    height: 794px;
    font-family: "Caveat", cursive;
  }
  .card-outside {
    position: absolute;
    left: 21px;
    top: 18px;
    width: 550px;
    height: 755px;
    border: 1px solid var(--rule);
    box-sizing: border-box;
    background: var(--paper);
    overflow: hidden;
  }
  .brand-tag {
    position: absolute;
    left: 391px;
    top: 197px;
    width: 132px;
    height: 132px;
    border-radius: 50%;
    background: var(--card-red);
    display: flex;
    align-items: center;
    justify-content: center;
    text-align: center;
  }
  .brand-tag__name {
    transform: rotate(180deg);
    color: var(--paper);
    font-size: 19px;
    font-weight: 600;
    line-height: 1;
    width: 96px;
  }
  .tag-string {
    position: absolute;
    left: 0;
    top: 0;
  }
  .front-photo {
    position: absolute;
    left: 0;
    top: 379px;
    width: 100%;
    height: 376px;
    background: linear-gradient(160deg, var(--photo-dark) 0%, var(--photo-mid) 40%, var(--photo-light) 60%, var(--photo-mid) 80%, var(--photo-dark) 100%);
  }
  .front-caption {
    position: absolute;
    left: 138px;
    top: 701px;
    width: 410px;
    height: 28px;
    background: var(--card-red);
  }
  .front-caption__text {
    position: absolute;
    left: 8px;
    bottom: -6px;
    margin: 0;
    color: var(--paper);
    font-size: 40px;
    font-weight: 400;
    white-space: nowrap;
    line-height: 1;
  }
  .card-inside {
    position: absolute;
    left: 630px;
    top: 18px;
    width: 549px;
    height: 755px;
    border: 15px solid var(--card-red);
    box-sizing: border-box;
    background: var(--paper);
  }
  .fold-line {
    position: absolute;
    left: 630px;
    top: 397px;
    width: 549px;
    border-top: 1px dashed var(--rule);
  }
  .inside-message {
    position: absolute;
    left: 630px;
    top: 544px;
    width: 549px;
    margin: 0;
    text-align: center;
    color: var(--ink);
    font-size: 27px;
    letter-spacing: 1px;
  }
</style>
</head>
<body>
<main class="sheet">
  <section class="card-outside">
    <div class="brand-tag"><span class="brand-tag__name">Bright Hearts Open Pages</span></div>
    <svg class="tag-string" width="550" height="400" aria-hidden="true">
      <circle cx="456" cy="322" r="3" fill="#ffffff"/>
      <path d="M456 324 C452 350 450 370 444 380" stroke="#666" stroke-width="1" fill="none"/>
      <path d="M456 324 C460 350 456 370 450 380" stroke="#666" stroke-width="1" fill="none"/>
    </svg>
    <div class="front-photo" role="img" aria-label="Black and white photo of two hands resting together on grass, one wearing a ring"></div>
    <div class="front-caption">
      <p class="front-caption__text">With your hand in mine...</p>
    </div>
  </section>

  <section class="card-inside"></section>
  <div class="fold-line"></div>
  <p class="inside-message">Everything is right in the world</p>
</main>
</body>
</html>
```